Coastal Learner Bureau business cards

Australian company about to start offering its services. We recruit international students to come to study English, vocational education and postgraduate courses in Australia. We help them find the institution and select the right city they want to come to Australia. We are a young, online oriented and supportive agency. Our clients are between 18 and 35 years old, mainly University students, young professionals or people with work experience. We provide much more information that any other agency offer. We administrate a Facebook group with more than 11.000 members that daily ask questions about general information when coming to Australia, while they are here and even after they leave the country

Target Market(s)

International students from South America, Central America and Europe

Industry/Entity Type

Student

Contact Information for Business Card

Tomas Bilbrea
Managing Director
tomas@kelvarin.com.au
www.kelvoria.com.au
+61 491058264
Melbourne, Australia

Font styles to use
Serif
Sans Serif

Colors

Designer to choose colors to be used in the design.

Requirements
Must have
• Horizontal design
• Standard business card size and shape. If font uses green or yellow colours, they will have to match the ones from the logo
Nice to have
• UPDATE: Use the contents of the green image to design one of the card sides. Use our logo in the background of that side as watermark.
• Passport image, or immigration stamps. A picture of the Yarra River (from Melbourne) would be cool as well.
Should not have
• Non-standard business card size and shape
• Not black as the background colour of any sides as we are not a VIP agency or a hight class service. We are orientes to young people and they like colours, pictures, something attractive.
• Vertical design
• NO YELLOW or BLACK AS THE BACKGROUND COLOUR OF ANY SIDE OF THE BIZ CARD

```html
<!DOCTYPE html>
<html lang="en">
<head>
<meta charset="utf-8">
<title>Coastal Learner Bureau – Business Cards</title>
<link href="https://fonts.googleapis.com/css2?family=Open+Sans:wght@400;600;700&display=swap" rel="stylesheet">
<style>
  :root {
    --green: #137a4a;
    --green-light: #1d9560;
    --green-dark: #0b5434;
    --yellow: #e2b714;
    --paper: #f7f7f5;
    --ink: #333333;
    --backdrop: #e4e6e5;
  }
  * { margin: 0; padding: 0; box-sizing: border-box; }
  html, body {
    width: 1200px; height: 900px; overflow: hidden;
    background: var(--backdrop);
    font-family: "Open Sans", Arial, sans-serif;
  }
  .canvas { position: relative; width: 1200px; height: 900px; }
  .card {
    position: absolute; left: 250px; width: 700px; height: 400px;
    overflow: hidden;
    box-shadow: 0 10px 28px rgba(0,0,0,0.22);
  }
  /* Front side */
  .card-front {
    top: 40px;
    background: linear-gradient(150deg, var(--green-dark) 0%, var(--green) 50%, var(--green-light) 100%);
  }
  .front-name {
    position: absolute; left: 0; right: 0; top: 150px;
    text-align: center; color: #ffffff;
    font-weight: 700; font-size: 44px; letter-spacing: 0.5px;
  }
  .tagline {
    position: absolute; left: 0; right: 0; top: 322px;
    display: flex; align-items: center; justify-content: center; gap: 14px;
    color: #ffffff; font-size: 15px; font-weight: 600;
  }
  .tagline .rule { width: 250px; height: 1px; background: rgba(255,255,255,0.75); }
  /* Back side */
  .card-back { top: 470px; background: var(--paper); }
  .back-name {
    position: absolute; left: 46px; top: 150px; width: 270px;
    color: var(--green); font-weight: 700; font-size: 30px; line-height: 1.15;
  }
  .contact {
    position: absolute; right: 40px; top: 96px;
    text-align: right; color: var(--ink); font-size: 15px; line-height: 1.55;
  }
  .contact .person { color: var(--green); font-weight: 700; font-size: 17px; text-transform: uppercase; }
  .contact .role { color: var(--yellow); font-weight: 600; font-size: 16px; text-transform: uppercase; }
  .contact .row { display: flex; justify-content: flex-end; align-items: center; gap: 8px; }
  .contact .icon { width: 14px; height: 14px; fill: var(--green); }
  .contact .spacer { width: 14px; }
  .footer-shape { position: absolute; left: 0; top: 0; width: 700px; height: 400px; }
  .website {
    position: absolute; right: 32px; top: 306px;
    color: #ffffff; font-size: 14px; letter-spacing: 2px; white-space: nowrap;
  }
</style>
</head>
<body>
<main class="canvas">

  <section class="card card-front" aria-label="Card front">
    <div class="front-name">Coastal Learner Bureau</div>
    <div class="tagline">
      <span class="rule"></span>
      <span>Hacemos más por ti!</span>
      <span class="rule"></span>
    </div>
  </section>

  <section class="card card-back" aria-label="Card back">
    <svg class="footer-shape" viewBox="0 0 700 400" aria-hidden="true">
      <path d="M700 296 L455 296 C428 296 418 316 400 336 C388 350 372 358 350 358 L0 358 L0 400 L700 400 Z" fill="var(--green)"/>
      <path d="M0 348 L345 348 C366 348 380 340 393 326 C410 306 422 288 455 288" fill="none" stroke="var(--yellow)" stroke-width="6"/>
    </svg>

    <div class="back-name">Coastal Learner Bureau</div>

    <div class="contact">
      <div class="person">Tomas Bilbrea</div>
      <div class="role">Managing Director</div>
      <div class="row"><span>Melbourne, Australia</span><span class="spacer"></span></div>
      <div class="row">
        <span>+61 491058264</span>
        <svg class="icon" viewBox="0 0 16 16" aria-hidden="true"><path d="M3 1.5 L6 1.5 L7 5 L5.2 6.2 C6 8 7.8 9.9 9.8 10.8 L11 9 L14.5 10 L14.5 13 C14.5 14 13.6 14.6 12.6 14.5 C6.8 13.8 2.2 9.2 1.5 3.4 C1.4 2.4 2 1.5 3 1.5 Z"/></svg>
      </div>
      <div class="row">
        <span>tomas@kelvarin.com.au</span>
        <svg class="icon" viewBox="0 0 16 16" aria-hidden="true"><path d="M1 3 H15 V13 H1 Z M2 4 L8 9 L14 4 Z" fill-rule="evenodd"/></svg>
      </div>
    </div>

    <div class="website">www.kelvoria.com.au</div>
  </section>

</main>
</body>
</html>
```